1876 Basins & Spouts Business Card

I'm wanting to get a business card designed. Our business is 1876 Basins & Spouts
Details for the card:

1876 Basins & Spouts
Name: Harold Vesk
Email: harold@1876basinsandspouts.com.au
Website: www.1876basinsandspouts.com.au
Mobile: 0438 260 947
Phone: 02 7481 3926

Font of Basins & Spouts is called Snell Roundhand. Not sue what font logo text is.

I'm thinking two sided but it doesn't have to be.

```html
<!DOCTYPE html>
<html lang="en">
<head>
<meta charset="utf-8">
<title>1876 Basins &amp; Spouts – Business Card</title>
<link rel="stylesheet" href="https://fonts.googleapis.com/css2?family=Roboto:wght@400;500;700&family=Open+Sans:wght@400&family=Poppins:wght@500&display=swap">
<style>
  :root {
    --page: #e4e4e4;
    --card-white: #ffffff;
    --card-black: #050505;
    --ink: #111111;
    --band-grey: #c4c4c4;
    --tagline-grey: #d6d6d6;
    --muted: #555555;
  }
  * { margin: 0; padding: 0; box-sizing: border-box; }
  html, body {
    width: 1200px; height: 1200px; overflow: hidden;
    background: var(--page);
  }
  .canvas { position: relative; width: 1200px; height: 1200px; }

  .card {
    position: absolute; left: 262px; width: 686px; height: 392px;
    box-shadow: 0 14px 22px rgba(0,0,0,0.18);
    overflow: hidden;
  }
  .card--front { top: 165px; background: var(--card-white); }
  .card--back  { top: 653px; background: var(--card-black); }

  /* Front */
  .brand__name {
    position: absolute; left: 376px; top: 66px;
    font-family: "Roboto", sans-serif; font-weight: 400;
    font-size: 22px; line-height: 26px; color: var(--ink);
    white-space: nowrap;
  }
  .brand__tagline {
    position: absolute; left: 461px; top: 101px;
    font-family: "Open Sans", sans-serif; font-size: 8.5px;
    color: var(--muted); white-space: nowrap;
  }
  .person {
    position: absolute; left: 46px; top: 248px;
    font-family: "Roboto", sans-serif; font-weight: 700;
    font-size: 24px; color: var(--ink);
  }
  .contacts {
    position: absolute; left: 46px; top: 300px; list-style: none;
    font-family: "Roboto", sans-serif; font-size: 16px; color: var(--ink);
  }
  .contacts li { display: flex; align-items: center; height: 22.5px; }
  .contacts svg { width: 14px; height: 14px; margin-right: 11px; flex: none; }

  .footer-band { position: absolute; left: 0; bottom: 0; width: 686px; height: 32px; }
  .website {
    position: absolute; left: 406px; bottom: 7px;
    font-family: "Poppins", sans-serif; font-weight: 500;
    font-size: 14.5px; color: var(--card-white); white-space: nowrap;
  }

  /* Back */
  .back-mark {
    position: absolute; left: 0; top: 150px; width: 100%;
    text-align: center;
    font-family: "Roboto", sans-serif; font-weight: 400;
    font-size: 40px; color: var(--card-white);
  }
  .back-tagline {
    position: absolute; left: 0; top: 220px; width: 100%;
    text-align: center;
    font-family: "Open Sans", sans-serif; font-size: 16px;
    color: var(--tagline-grey);
  }
</style>
</head>
<body>
<main class="canvas">

  <section class="card card--front" aria-label="Business card front">
    <div class="brand__name">1876 Basins &amp; Spouts</div>
    <div class="brand__tagline">Pairing enduring elegance with everyday usefulness</div>

    <h1 class="person">Harold Vesk</h1>

    <ul class="contacts">
      <li>
        <svg viewBox="0 0 24 24" aria-hidden="true"><path fill="#111" d="M6.6 10.8a15.1 15.1 0 0 0 6.6 6.6l2.2-2.2a1 1 0 0 1 1-.25 11.4 11.4 0 0 0 3.6.57 1 1 0 0 1 1 1V20a1 1 0 0 1-1 1A17 17 0 0 1 3 4a1 1 0 0 1 1-1h3.5a1 1 0 0 1 1 1c0 1.25.2 2.450.57 3.57a1 1 0 0 1-.25 1z"/></svg>
        02 7481 3926
      </li>
      <li>
        <svg viewBox="0 0 24 24" aria-hidden="true"><rect x="6" y="1.5" width="12" height="21" rx="2" fill="none" stroke="#111" stroke-width="2.2"/><rect x="10" y="18" width="4" height="1.6" fill="#111"/></svg>
        0438 260 947
      </li>
      <li>
        <svg viewBox="0 0 24 24" aria-hidden="true"><path fill="#111" d="M2 6h20v12H2z"/><path fill="none" stroke="#fff" stroke-width="1.6" d="M2.5 6.5 12 13l9.5-6.5"/></svg>
        harold@1876basinsandspouts.com.au
      </li>
    </ul>

    <svg class="footer-band" viewBox="0 0 686 32" preserveAspectRatio="none" aria-hidden="true">
      <rect x="0" y="25" width="686" height="7" fill="var(--band-grey)"/>
      <polygon points="394,0 686,0 686,32 363,32" fill="var(--card-black)"/>
    </svg>
    <div class="website">www.1876basinsandspouts.com.au</div>
  </section>

  <section class="card card--back" aria-label="Business card back">
    <div class="back-mark">Basins &amp; Spouts</div>
    <div class="back-tagline">Pairing enduring elegance with everyday usefulness</div>
  </section>

</main>
</body>
</html>
```